13 Varno - new website design project

Our company Varno Electrical is developing a new lead generation website focused on Electrical, LED Lighting and Solar Power. We need a high converting website.

Example of our current website is www.varnoelectrical-example.com.au You can take content from this website for this new design. Our colours are red, black and white. For our new website we would like to promote Varno, Spark Every Day. Please listen to the jingle.

The below link is the company jingle that we have developed.
http://www.tunecraftdemo.com.au/vrn-tc-v1/

The key for this brief is to generate leads for Electrical, LED Lighting (for commercial) and Solar Power & Storage.

Target Market(s)

Business owners in Melbourne Victoria

Number of Pages Required

4 page

Colors
ec1f27
ffffff

Requirements
Must have
• This page must be clean, be in line with company branding and a high converting lead website.

```html
<!DOCTYPE html>
<html lang="en">
<head>
<meta charset="utf-8">
<title>Varno Electrical</title>
<link rel="stylesheet" href="https://fonts.googleapis.com/css2?family=Roboto:ital,wght@0,300;0,400;0,500;0,700;0,900;1,300;1,400&display=swap">
<style>
:root{
  --red:#e8393e;
  --red-light:#f27a7a;
  --red-deep:#e02c33;
  --dark:#3a3b3f;
  --gray-hero:#6b6c72;
  --gray-hero-dark:#505157;
  --light-bg:#f3f3f4;
  --white:#ffffff;
  --text:#2a2a2a;
  --muted:#555;
  --line:#d9d9d9;
}
*{box-sizing:border-box;margin:0;padding:0}
html,body{width:1200px;height:2423px;overflow:hidden}
body{font-family:"Roboto",Arial,sans-serif;color:var(--text);background:var(--white);position:relative}
.dashed{border-top:1px dashed rgba(255,255,255,.75);width:1096px;margin:0 auto}
.dashed.red{border-top-color:var(--red)}

/* Hero */
.hero{position:relative;height:543px;background:linear-gradient(100deg,var(--gray-hero-dark) 0%,var(--gray-hero) 60%,#7b7c82 100%);overflow:hidden;color:var(--white)}
.hero .sheen{position:absolute;inset:0}
.site-header{position:absolute;top:0;left:0;right:0;height:66px;border-bottom:1px solid rgba(255,255,255,.18)}
.brand{position:absolute;left:58px;top:14px;display:flex;align-items:center;gap:10px;font-weight:900;font-size:34px;letter-spacing:-.5px;color:var(--white)}
.brand .dot{width:22px;height:22px;border-radius:50%;background:var(--white)}
.main-nav{position:absolute;left:352px;top:24px;display:flex}
.main-nav a{color:var(--white);text-decoration:none;font-size:16px;font-weight:500;margin-right:42px}
.header-actions{position:absolute;right:46px;top:15px;display:flex;gap:8px}
.btn-outline{border:2px solid var(--white);border-radius:18px;color:var(--white);font-size:13px;padding:7px 12px;font-weight:500}
.btn-solid{background:var(--white);border-radius:18px;color:#111;font-size:13px;padding:9px 14px;font-weight:500}
.hero-copy{position:absolute;left:58px;top:218px;width:550px;text-align:center}
.hero-kicker{display:flex;align-items:center;justify-content:center;gap:14px;font-size:30px;font-weight:400;letter-spacing:.5px}
.hero-kicker .bar{width:50px;height:9px;background:rgba(255,255,255,.6)}
.hero-title{font-size:78px;font-weight:900;letter-spacing:1px;line-height:1;margin-top:6px;text-shadow:0 3px 4px rgba(0,0,0,.35)}
.hero-call{font-size:24px;margin-top:8px;letter-spacing:.5px}
.hero-glow{position:absolute;left:830px;top:80px;width:300px;height:320px;border-radius:50%;background:radial-gradient(circle at 50% 45%,rgba(246,194,26,.85) 0%,rgba(246,194,26,.35) 35%,rgba(246,194,26,0) 70%)}

/* Welcome */
.welcome{height:111px;background:linear-gradient(90deg,var(--red-deep),var(--red-light));color:var(--white);text-align:center;padding-top:6px}
.welcome h2{font-size:22px;font-weight:500;margin-bottom:10px}
.welcome p{font-size:12.5px;line-height:20px;width:1096px;margin:14px auto 0}

/* Section titles */
.section-title{text-align:center;font-size:22px;font-weight:700;color:var(--text)}
.section-title span{color:var(--red)}

/* Services */
.services{height:343px;background:var(--light-bg);padding-top:18px}
.services .section-title{margin-bottom:8px}
.service-grid{display:flex;justify-content:space-between;width:1096px;margin:60px auto 0}
.service-card{width:347px;height:154px;position:relative}
.service-photo{width:347px;height:154px}
.service-icon{position:absolute;left:149px;top:-22px;width:48px;height:48px;border-radius:50%;background:var(--red);border:3px solid rgba(255,255,255,.6);display:flex;align-items:center;justify-content:center}
.service-label{position:absolute;left:14px;right:14px;top:132px;height:42px;background:linear-gradient(90deg,var(--red-deep),var(--red-light));color:var(--white);font-size:17px;font-weight:500;display:flex;align-items:center;justify-content:center;border-radius:3px}

/* Why choose */
.why{height:386px;background:linear-gradient(90deg,var(--red-deep),var(--red-light));color:var(--white);padding-top:22px}
.why h2{text-align:center;font-size:22px;font-weight:700;margin-bottom:12px}
.why-grid{position:relative;width:1096px;margin:30px auto 0;height:280px}
.why-line{position:absolute;top:46px;height:1px;background:rgba(255,255,255,.7)}
.why-item{position:absolute;width:250px;text-align:center;top:0}
.why-circle{width:92px;height:92px;border-radius:50%;background:var(--dark);border:3px solid rgba(255,255,255,.85);margin:0 auto;display:flex;align-items:center;justify-content:center}
.why-item h3{font-size:18px;font-weight:700;margin-top:24px}
.why-item.alt h3{color:#111}
.why-item p{font-size:12.5px;line-height:20px;margin-top:14px}

/* Work */
.work{height:300px;background:var(--white);padding-top:18px}
.work .dashed{margin-top:16px}
.client-row{display:flex;margin-top:32px}
.client{width:240px;height:58px;display:flex;align-items:center;justify-content:center;font-size:24px;font-weight:500;color:var(--text);border-right:1px solid var(--line)}
.client:last-child{border-right:0}
.photo-row{display:flex;margin-top:4px}
.work-photo{width:240px;height:123px}

/* Testimonials */
.testimonials{height:288px;background:var(--light-bg);padding-top:22px;position:relative}
.testimonials .dashed{margin-top:14px}
.quote-row{width:1096px;margin:40px auto 0;display:flex;position:relative}
.quote{width:548px;display:flex;gap:22px;align-items:flex-start}
.quote.left{justify-content:flex-end;padding-right:30px;text-align:right}
.quote.right{padding-left:30px}
.quote-divider{position:absolute;left:547px;top:0;height:90px;border-left:1px dashed #999}
.quote p{font-size:13px;line-height:20px;font-style:italic;color:var(--muted);width:400px}
.quote cite{display:block;font-style:normal;font-size:12.5px;color:#111;margin-top:10px}
.avatar{width:78px;height:78px;border-radius:50%;background:radial-gradient(circle at 50% 40%,#d9c4b4,#9a8b80);flex-shrink:0;margin-top:-4px}
.skyline{position:absolute;left:0;bottom:0;width:1200px;height:66px;background:linear-gradient(0deg,var(--red) 0%,rgba(232,57,62,.85) 45%,rgba(232,57,62,0) 100%)}

/* Footer */
.site-footer{height:452px;background:linear-gradient(90deg,var(--red-deep),var(--red-light));color:var(--white);position:relative}
.footer-cols{width:1096px;margin:0 auto;display:flex;padding-top:52px}
.footer-col{width:281px}
.footer-col h4{font-size:18px;font-weight:500;margin-bottom:20px}
.footer-col p{font-size:13px;line-height:20px;margin-bottom:14px;max-width:253px}
.footer-col p.nowrap{white-space:nowrap;max-width:none;font-size:12px}
.footer-col strong{font-weight:700}
.socials{display:flex;gap:12px;margin-top:4px}
.socials span{width:14px;height:14px;border-radius:50%;background:var(--white)}
.form{width:253px}
.form .row{display:flex;gap:19px;margin-bottom:12px}
.field{background:var(--white);height:30px;border-radius:2px;font-size:12px;color:#999;padding:8px 10px}
.field.half{width:117px}
.field.area{height:64px}
.btn-send{display:inline-block;background:var(--white);color:#111;font-size:12.5px;font-weight:500;padding:9px 18px;border-radius:2px;margin-top:6px}
.map{width:253px;height:226px;background:linear-gradient(135deg,#dfe6cf,#cfd9e8 60%,#b9cde6)}
.footer-bottom{position:absolute;left:52px;right:52px;top:384px;border-top:1px solid rgba(255,255,255,.6);height:68px;display:flex;align-items:center;justify-content:space-between;font-size:12px;font-weight:700}
.footer-brand{font-size:30px;font-weight:900;color:var(--white)}
</style>
</head>
<body>

<section class="hero">
  <svg class="sheen" width="1200" height="543" aria-hidden="true">
    <polygon points="260,0 1200,0 1200,543 820,543" fill="rgba(255,255,255,.07)"/>
  </svg>
  <header class="site-header">
    <div class="brand"><span class="dot"></span>Varno</div>
    <nav class="main-nav">
      <a href="#">HOME</a><a href="#">ABOUT US</a><a href="#">SERVICES</a><a href="#">OUR WORK</a><a href="#">CONTACT</a>
    </nav>
    <div class="header-actions"><span class="btn-outline">Log In</span><span class="btn-solid">Request a Quote</span></div>
  </header>
  <div class="hero-glow" role="img" aria-label="Glowing yellow light bulb illustration"></div>
  <div class="hero-copy">
    <div class="hero-kicker"><span class="bar"></span>DO YOU NEED A NEW<span class="bar"></span></div>
    <h1 class="hero-title">ELECTRICIAN?</h1>
    <p class="hero-call">Call Varno Electric at (13 7319)</p>
  </div>
</section>

<section class="welcome">
  <h2>Welcome to Varno Electrical</h2>
  <div class="dashed"></div>
  <p>Varno Electrical was formed to be an expert Electricity Contracting Company providing services to all Residential and Commercial Customers. With over 10 years of experience, Varno Electrical has developed a highly-experienced team of professionals that ensure all our customer expectations are met.</p>
</section>

<section class="services">
  <h2 class="section-title">Our <span>Services</span></h2>
  <div class="dashed red"></div>
  <div class="service-grid">
    <div class="service-card">
      <div class="service-photo" role="img" aria-label="Electrician testing a switchboard with a multimeter" style="background:linear-gradient(135deg,#5a4a3c,#c9c2b6 55%,#2f3a55)"></div>
      <div class="service-icon"><svg width="22" height="22" viewBox="0 0 22 22"><path d="M6 16l10-10M9 5l8 8M5 9l8 8" stroke="#fff" stroke-width="2" fill="none" stroke-linecap="round"/></svg></div>
      <div class="service-label">Electrical</div>
    </div>
    <div class="service-card">
      <div class="service-photo" role="img" aria-label="Warehouse interior with LED high bay lighting" style="background:linear-gradient(180deg,#9aa6b4,#e3e6ea 50%,#8c8576)"></div>
      <div class="service-icon"><svg width="22" height="22" viewBox="0 0 22 22"><circle cx="11" cy="9" r="5" stroke="#fff" stroke-width="2" fill="none"/><path d="M9 16h4M9 19h4" stroke="#fff" stroke-width="2"/></svg></div>
      <div class="service-label">Led Lighting</div>
    </div>
    <div class="service-card">
      <div class="service-photo" role="img" aria-label="Installers fitting solar panels on a roof" style="background:linear-gradient(160deg,#c7d2de,#5c6f8c 55%,#2e3c55)"></div>
      <div class="service-icon"><svg width="22" height="22" viewBox="0 0 22 22"><rect x="3" y="6" width="16" height="10" stroke="#fff" stroke-width="2" fill="none"/><path d="M8 6v10M14 6v10M3 11h16" stroke="#fff" stroke-width="1.5"/></svg></div>
      <div class="service-label">Solar Power</div>
    </div>
  </div>
</section>

<section class="why">
  <h2>Why Choose Us</h2>
  <div class="dashed"></div>
  <div class="why-grid">
    <div class="why-line" style="left:180px;width:150px"></div>
    <div class="why-line" style="left:455px;width:180px"></div>
    <div class="why-line" style="left:740px;width:155px"></div>
    <div class="why-item" style="left:1px">
      <div class="why-circle"><svg width="40" height="40" viewBox="0 0 40 40"><circle cx="20" cy="20" r="14" stroke="#fff" stroke-width="3" fill="none" stroke-dasharray="5 3"/><circle cx="20" cy="18" r="6" fill="#fff"/><rect x="17" y="24" width="6" height="5" fill="#fff"/></svg></div>
      <h3>Professional Service</h3>
      <p>When you hire a Varno Electrical Electrician you will get a professional and well-presented Electrician that comes skilled and ready to do the job.</p>
    </div>
    <div class="why-item" style="left:282px">
      <div class="why-circle"><svg width="40" height="40" viewBox="0 0 40 40"><path d="M9 21l8 8 15-17" stroke="#fff" stroke-width="6" fill="none" stroke-linecap="round" stroke-linejoin="round"/></svg></div>
      <h3>5 Year Guarantee</h3>
      <p>You can buy with confidence as all of our work has a 5 year workmanship guarantee. For your peace of mind, we unconditionally back our electrical work. We will come back to fix any problems at our own expense.</p>
    </div>
    <div class="why-item alt" style="left:563px">
      <div class="why-circle"><svg width="40" height="40" viewBox="0 0 40 40"><circle cx="20" cy="16" r="7" fill="#fff"/><path d="M20 4v4M9 9l3 3M31 9l-3 3M6 18h4M30 18h4" stroke="#fff" stroke-width="2"/><path d="M8 28c4 6 20 6 24 0" stroke="#fff" stroke-width="3" fill="none"/></svg></div>
      <h3>Environmentally friendly</h3>
      <p>We a committed to reducing carbon emissions by installing Solar Power and upgrading sites to LED Lighting. In addition to reducing the carbon emissions we recycle Fluorescent Tubes, Highbay Globes, Metal and Cardboard.</p>
    </div>
    <div class="why-item" style="left:840px">
      <div class="why-circle"><svg width="40" height="40" viewBox="0 0 40 40"><rect x="7" y="11" width="26" height="19" rx="2" stroke="#fff" stroke-width="3" fill="none"/><path d="M24 20h9" stroke="#fff" stroke-width="3"/></svg></div>
      <h3>Value for Money</h3>
      <p>We provide extremely competitive pricing, which means you get value for money on quality that is comparable to the best in the industry.</p>
    </div>
  </div>
</section>

<section class="work">
  <h2 class="section-title">Our <span>Work</span></h2>
  <div class="dashed red"></div>
  <div class="client-row">
    <div class="client">Lumora Retail</div>
    <div class="client">Outback Supply Co</div>
    <div class="client">Boardline</div>
    <div class="client">Harlow Signs</div>
    <div class="client">Steelvane</div>
  </div>
  <div class="photo-row">
    <div class="work-photo" role="img" aria-label="Retail store interior with new lighting" style="background:linear-gradient(180deg,#b7bcc6,#6f7c95)"></div>
    <div class="work-photo" role="img" aria-label="Warehouse with racking and lighting" style="background:linear-gradient(180deg,#8a8d92,#5f5445)"></div>
    <div class="work-photo" role="img" aria-label="Building supplies storefront exterior" style="background:linear-gradient(180deg,#d7e3f0,#c2393f 60%,#8d8f93)"></div>
    <div class="work-photo" role="img" aria-label="Sign workshop interior" style="background:linear-gradient(180deg,#9da1a7,#58524a)"></div>
    <div class="work-photo" role="img" aria-label="Steel warehouse interior" style="background:linear-gradient(180deg,#6e7a8c,#3c4250)"></div>
  </div>
</section>

<section class="testimonials">
  <h2 class="section-title">What <span>People Say</span></h2>
  <div class="dashed red"></div>
  <div class="quote-row">
    <div class="quote-divider"></div>
    <div class="quote left">
      <div><p>Duis aute irure dolor in reprehenderit in voluptate velit esse cillum dolore eu fugiat nulla pariatur. Excepteur sint occaecat cupidatat non proident, sunt in culpa qui officia deserunt mollit.</p><cite>Reid Malloy, Operations Manager</cite></div>
      <div class="avatar" role="img" aria-label="Portrait of Reid Malloy"></div>
    </div>
    <div class="quote right">
      <div class="avatar" role="img" aria-label="Portrait of Tessa Quinlan"></div>
      <div><p>Provident, similique sunt in culpa qui officia deserunt mollitia animi, id est laborum et dolorum fuga. Et harum quidem rerum facilis est et expedita distinctio. Nam libero tempore, cum soluta nobis.</p><cite>Tessa Quinlan, Creative Designer</cite></div>
    </div>
  </div>
  <div class="skyline" role="img" aria-label="City skyline silhouette with airport and planes"></div>
</section>

<footer class="site-footer">
  <div class="footer-cols">
    <div class="footer-col">
      <h4>Contact Us</h4>
      <p>Please feel free to contact us for any issue. Our staff is available to you from 9AM until 5PM on weekdays.</p>
      <p><strong>Phone:</strong> 13 73 19</p>
      <p><strong>Office:</strong> 4/88 Larkin St Ashwood</p>
      <p class="nowrap"><strong>Email:</strong> service@varnoelectrical-example.com.au</p>
      <div class="socials"><span></span><span></span><span></span><span></span><span></span></div>
    </div>
    <div class="footer-col">
      <h4>Feel Free to Mail</h4>
      <div class="form">
        <div class="row"><div class="field half">Name *</div><div class="field half">Email *</div></div>
        <div class="row"><div class="field" style="width:253px">Subject</div></div>
        <div class="row"><div class="field area" style="width:253px">Write Your Message Here...</div></div>
        <span class="btn-send">SEND MESSAGE</span>
      </div>
    </div>
    <div class="footer-col">
      <h4>Headquarters</h4>
      <div class="map" role="img" aria-label="Street map showing the headquarters location"></div>
    </div>
    <div class="footer-col">
      <h4>About Team</h4>
      <p>Enim congue blandit. Lorem ipsum dolor sit amet, consectetur adipiscing elit. Quisque consectetur interdum finibus. Vestibulum ante ipsum primis in faucibus orci. luctus et ultrices posuere.</p>
      <p>Cubilia cras blandit finibus ipsum, id porttitor arcu volutpat a. Integer iaculis erat nec justo malesuada faucibus vel tempus sapien. Vivamus aliquam euismod tristique.</p>
    </div>
  </div>
  <div class="footer-bottom">
    <span>Copyright © Varno Electrical</span>
    <span class="footer-brand">Varno</span>
    <span>All rights reserved</span>
  </div>
</footer>

</body>
</html>
```